Exclusive beauty salon needs a price list or services booklet

I need a new very attractive flyer for my beauty salon, containing information on the different services and their prices.
In attachment you can find a pdf of the "old" one, but I'd love to have a beautifully designed new one!
I'd love to have a booklet in format 148 x 148 mm, or in US format, containing 12 or 16 pages, but if you can offer other nice looking designs they are welcome!
The services that need to come in the booklet with their prices can all be found on my website: www.atelierverano.be, starting with
Gelaatsverzorging
Wimperverlenging
Suikerontharing
Wimperlifting
Permanente Make Up
Airbrush Tanning

Target Market(s)

woman from 20 to 89 years old

Industry/Entity Type

Beauty Salon

Font styles to use
Sans Serif

Colors

Designer to choose colors to be used in the design.

Requirements
Must have
• a classy nice look, it must contain details about the services from my beauty salon and their prices, and nice pictures.
• The Names, prices and explanations of the services can easily be found on my website: www.atelierverano.be
Nice to have
• In attachment you can find the "old" price list in pdf, what I need now is a "new booklet" with the new logo and updated services price list.
• I need a very nice and attractive looking booklet, classy chique, Paris chique, looking very expensive.
Should not have
• Not too much colors, not too curly, but still feminine

```html
<!DOCTYPE html>
<html lang="nl">
<head>
<meta charset="utf-8">
<title>Wimperlifting – LUXA-methode</title>
<link rel="stylesheet" href="https://fonts.googleapis.com/css2?family=Source+Sans+3:ital,wght@1,400&display=swap">
<style>
  :root {
    --page: #ffffff;
    --panel: #a7a8ab;
    --ink: #ffffff;
    --frame: #ffffff;
  }
  html, body {
    margin: 0;
    padding: 0;
    width: 1200px;
    height: 868px;
    overflow: hidden;
    background: var(--page);
  }
  .spread {
    position: relative;
    width: 1200px;
    height: 868px;
  }
  .panel {
    position: absolute;
    left: 34px;
    top: 33px;
    width: 1130px;
    height: 797px;
    background: var(--panel);
  }
  .intro-frame {
    position: absolute;
    left: 283px;
    top: 203px;
    width: 640px;
    height: 441px;
    border: 1.5px solid var(--frame);
    box-sizing: border-box;
  }
  .intro-text {
    position: absolute;
    left: 317px;
    top: 251px;
    width: 600px;
    font-family: "Source Sans 3", "Myriad Pro", sans-serif;
    font-style: italic;
    font-weight: 400;
    font-size: 24px;
    letter-spacing: 0.6px;
    line-height: 32.5px;
    color: var(--ink);
  }
  .intro-text p {
    margin: 0 0 11px 0;
    white-space: nowrap;
  }
</style>
</head>
<body>
  <main class="spread">
    <div class="panel"></div>
    <div class="intro-frame"></div>
    <section class="intro-text">
      <p>Het hebben van mooie, lange en volumineuze wimpers<br>
      staat hoog op het verlanglijstje van vele vrouwen. Het<br>
      liefst heeft men de wimpers mooi gelift voor een open<br>
      blik die de ogen optisch groter maakt. Niet voor niets is<br>
      mascara één van de best verkochte make-upproducten.</p>
      <p>De nieuwe en revolutionaire LUXA-methode zorgt echter<br>
      na slechts 1 behandeling van 60 minuten, gedurende<br>
      minimaal 6 weken voor lange, volle en mooi gelifte<br>
      wimpers. Dit alles, zonder dat daar een wimperkrultang<br>
      of dikke lagen mascara aan te pas hoeven te komen!</p>
    </section>
  </main>
</body>
</html>
```